BrivoTerna. Lantern of the Steady Harvest. Business card

Professional business card for BrivoTerna (Lantern of the Steady Harvest)
My rationale: Strategy-> Execution-> Results-> Value that lead to the BrivoTerna name: We put the Lantern of the Steady Harvest.
We deliver value to our customers helping them at defining a good strategy (cyan arrow). 90% of well formulated strategies fail due to poor execution so we also consider strategical execution very important (green arrow). Due to the execution we obtain the results (blue arrow). Finally, the results provide feedback to redefine strategy, and the new strategy has to be executed and new results obtained providing new feedback and on and on. It's like a wheel that finally, must create corporate value: value for shareholders, staholders, employees, providers...-

Target Market(s)

CEOs and steering comitees , invewrnent funds

Industry/Entity Type

Business Consultant

Contact Information for Business Card

Teodoro Vinsquel
CEO & Founder
teodoro.vinsquel@brivoterna-example.com
Mobile: +34 655.803.912
www.brivoterna-example.com

Colors

Designer to choose colors to be used in the design.

Requirements
Nice to have
• Nice to hace the words: Strategy, execution, results
• Nice to vave the claim: Lantern of the Steady Harvest
• The three colors should be shown:
• cyan for STRATEGY
• green for EXECUTION
• blue for RESULTS
Should not have
• Complete black background

```html
<!DOCTYPE html>
<html lang="en">
<head>
<meta charset="utf-8">
<title>BrivoTerna business card</title>
<link rel="stylesheet" href="https://fonts.googleapis.com/css2?family=Encode+Sans+Condensed:wght@700&family=Arimo:wght@400&display=swap">
<style>
  :root {
    --backdrop: #d6d7d9;
    --card-white: #ffffff;
    --brand-blue: #0a2f95;
    --card-blue: #0334a0;
    --strategy-cyan: #0fb0e8;
    --execution-green: #9bcb36;
    --results-blue: #0a2f95;
    --ink: #2e2e2e;
    --shadow: rgba(0, 0, 0, 0.35);
  }
  * { margin: 0; padding: 0; box-sizing: border-box; }
  html, body {
    width: 1200px;
    height: 802px;
    overflow: hidden;
    background: var(--backdrop);
  }
  .sheet { position: relative; width: 1200px; height: 802px; }
  .card {
    position: absolute;
    top: 274px;
    width: 443px;
    height: 265px;
    overflow: hidden;
    box-shadow: 2px 3px 6px var(--shadow);
  }
  .card--front { left: 136px; background: var(--card-white); }
  .card--back { left: 624px; background: var(--card-blue); }

  .stage-bars {
    position: absolute;
    left: 0;
    bottom: 0;
    width: 156px;
    height: 225px;
  }

  .wordmark {
    font-family: "Encode Sans Condensed", "Arial Narrow", sans-serif;
    font-weight: 700;
    letter-spacing: -1px;
    line-height: 1;
    white-space: nowrap;
  }
  .card--front .wordmark {
    position: absolute;
    left: 174px;
    top: 56px;
    font-size: 41px;
    color: var(--brand-blue);
  }
  .tagline-front {
    position: absolute;
    left: 174px;
    top: 97px;
    font-family: "Arimo", Arial, sans-serif;
    font-size: 11px;
    letter-spacing: 0.3px;
    color: var(--ink);
    white-space: nowrap;
  }
  .person {
    position: absolute;
    left: 174px;
    top: 145px;
    font-family: "Arimo", Arial, sans-serif;
    white-space: nowrap;
  }
  .person__name { font-size: 18px; color: var(--brand-blue); line-height: 1.1; }
  .person__role { font-size: 12.5px; color: var(--ink); line-height: 1.3; }
  .contacts {
    position: absolute;
    left: 174px;
    top: 194px;
    list-style: none;
    font-family: "Arimo", Arial, sans-serif;
    font-size: 12px;
    color: var(--ink);
    white-space: nowrap;
  }
  .contacts li { display: flex; align-items: center; gap: 4px; height: 16px; }
  .contacts svg { width: 13px; height: 13px; fill: var(--brand-blue); flex: none; }

  .card--back .wordmark {
    position: absolute;
    left: 0;
    right: 0;
    top: 140px;
    text-align: center;
    font-size: 44px;
    color: var(--card-white);
  }
  .tagline-back {
    position: absolute;
    left: 0;
    right: 0;
    top: 216px;
    text-align: center;
    font-family: "Arimo", Arial, sans-serif;
    font-size: 13px;
    letter-spacing: 0.2px;
    color: var(--card-white);
    white-space: nowrap;
  }
</style>
</head>
<body>
<main class="sheet">
  <section class="card card--front" aria-label="Business card front">
    <svg class="stage-bars" viewBox="0 0 156 225" role="img" aria-label="Three rising bars: cyan strategy, green execution, blue results">
      <rect x="0" y="150" width="44" height="75" fill="var(--strategy-cyan)"/>
      <rect x="54" y="80" width="44" height="145" fill="var(--execution-green)"/>
      <rect x="108" y="0" width="44" height="225" fill="var(--results-blue)"/>
    </svg>
    <div class="wordmark">BrivoTerna</div>
    <p class="tagline-front">STRATEGY, EXECUTION, RESULTS</p>
    <div class="person">
      <p class="person__name">Teodoro Vinsquel</p>
      <p class="person__role">CEO &amp; Founder</p>
    </div>
    <ul class="contacts">
      <li>
        <svg viewBox="0 0 16 16" aria-hidden="true"><path d="M1 6c0-2 3-3 7-3s7 1 7 3v1h-3.5V5.5h-7V7H1z"/><path d="M3.5 8.5 5 7h6l1.5 1.5V13h-9z"/></svg>
        +34 655.803.912
      </li>
      <li>
        <svg viewBox="0 0 16 16" aria-hidden="true"><path d="M1 3h14v10H1z"/><path d="M1.8 3.8 8 9l6.2-5.2" fill="none" stroke="#fff" stroke-width="1.3"/></svg>
        teodoro.vinsquel@brivoterna-example.com
      </li>
      <li>
        <svg viewBox="0 0 16 16" aria-hidden="true"><circle cx="8" cy="8" r="7"/><path d="M4 5c2 0 2 2 4 2s1 3-1 3-1 3-2 3M10 3c0 2 2 2 3 3" fill="none" stroke="#fff" stroke-width="1.1"/></svg>
        www.brivoterna-example.com
      </li>
    </ul>
  </section>

  <section class="card card--back" aria-label="Business card back">
    <div class="wordmark">BrivoTerna</div>
    <p class="tagline-back">LANTERN OF THE STEADY HARVEST</p>
  </section>
</main>
</body>
</html>
```